Business Cards Design for the electrical wholesaler: clean bold dynamic :)

We need a business card design that would follow our latest brand guidelines. As an electrical wholesaler we want to bring a fresh look and feel into the industry. The design should be clean bold and dynamic. It should come alive with the renewed energy of our green colour. Our grey colour should keep things balanced and complement the notion of maturity and responsibility. We employ Lato as a corporate font however are not bound by this font and we’re open to interpretation here.

Target Market(s)

Electrical contractors

Industry/Entity Type

Business

Contact Information for Business Card

Logo
Name & Surname: Halyna Dorosh
Job Title: Director of Marketing
Email: halya.dorosh@quillmail.example
Cell phone: XXX.XXX.XXXX
Address: 20517 - 87 Ave. Edmonton, AB, Canada. T6K 4N8
Business Phone: 780.555.0184
Website: www.brovix.example

Font styles to use
Other font styles liked:
• Lato

Requirements
Must have
• Logo & website
Nice to have
• Brand elements - some of them you may find in the attached Brand Guidelines (e.g. three lines on the background signifying "W")

```html
<!DOCTYPE html>
<html lang="en">
<head>
<meta charset="utf-8">
<title>Brovix Business Card</title>
<link href="https://fonts.googleapis.com/css2?family=Exo+2:wght@500;600&family=Lato:wght@400;700&display=swap" rel="stylesheet">
<style>
  :root {
    --page: #3b3b3c;
    --card: #1e1e1f;
    --green: #7dc21e;
    --grey: #c9c9c9;
    --text: #f2f2f2;
    --muted: #d8d8d8;
  }
  * { box-sizing: border-box; margin: 0; padding: 0; }
  html, body { width: 799px; height: 1200px; overflow: hidden; }
  body {
    background: var(--page);
    font-family: "Lato", sans-serif;
    position: relative;
  }
  .card {
    position: absolute;
    left: 100px;
    width: 600px;
    height: 343px;
    background: var(--card);
    border-radius: 22px;
    overflow: hidden;
    box-shadow: 0 14px 30px rgba(0,0,0,0.35);
  }
  .card--front { top: 115px; }
  .card--back { top: 715px; }

  .brand {
    display: flex;
    align-items: center;
    gap: 14px;
    font-family: "Lato", sans-serif;
    font-weight: 700;
    color: var(--grey);
    letter-spacing: 0.5px;
  }
  .brand__dot {
    border-radius: 50%;
    background: var(--green);
    flex: none;
  }
  .card--front .brand {
    position: absolute;
    left: 0; right: 0; top: 128px;
    justify-content: center;
    font-size: 80px;
    line-height: 1;
  }
  .card--front .brand__dot { width: 58px; height: 58px; }

  .card--back .brand {
    position: absolute;
    left: 34px; top: 30px;
    font-size: 40px;
    line-height: 1;
    gap: 10px;
  }
  .card--back .brand__dot { width: 30px; height: 30px; }

  .stripes {
    position: absolute;
    left: 0; top: 0;
    width: 600px; height: 343px;
  }
  .stripes path { fill: var(--green); }

  .contact {
    position: absolute;
    left: 34px; top: 112px;
    width: 300px;
    color: var(--text);
  }
  .contact__name {
    font-family: "Exo 2", sans-serif;
    font-weight: 600;
    font-size: 27px;
    color: var(--green);
    line-height: 1.1;
  }
  .contact__title {
    font-size: 15px;
    color: var(--muted);
    margin-top: 3px;
  }
  .contact__address {
    font-size: 14px;
    line-height: 1.45;
    margin-top: 16px;
    color: var(--muted);
  }
  .contact__list {
    list-style: none;
    margin-top: 12px;
    font-size: 14px;
    line-height: 1.9;
    color: var(--muted);
  }
  .contact__item { display: flex; align-items: center; gap: 8px; }
  .icon { width: 15px; height: 15px; flex: none; }
</style>
</head>
<body>

<section class="card card--front" aria-label="Card front">
  <div class="brand"><span class="brand__dot"></span>brovix</div>
</section>

<section class="card card--back" aria-label="Card back">
  <svg class="stripes" viewBox="0 0 600 343" aria-hidden="true">
    <path d="M348 343 V82 Q348 38 392 38 H428 Q448 38 448 58 V343 Z"/>
    <path d="M472 343 V130 Q472 95 507 95 H524 Q542 95 542 113 V343 Z"/>
    <path d="M564 343 V180 Q564 152 592 152 H600 V343 Z"/>
  </svg>

  <div class="brand"><span class="brand__dot"></span>brovix</div>

  <div class="contact">
    <p class="contact__name">Halyna Dorosh</p>
    <p class="contact__title">Director of Marketing</p>
    <p class="contact__address">20517 - 87 Ave. Edmonton,<br>AB, Canada T6K 4N8</p>
    <ul class="contact__list">
      <li class="contact__item">
        <svg class="icon" viewBox="0 0 16 16" aria-hidden="true">
          <circle cx="8" cy="8" r="8" fill="#7dc21e"/>
          <path d="M5.2 4.2l1.4 0 .6 1.8-.9.7c.4.9 1.1 1.6 2 2l.7-.9 1.8.6v1.4c0 .5-.4.8-.9.8A5.6 5.6 0 0 1 4.4 5c0-.5.3-.8.8-.8z" fill="#1e1e1f"/>
        </svg>
        +1 780.555.0184
      </li>
      <li class="contact__item">
        <svg class="icon" viewBox="0 0 16 16" aria-hidden="true">
          <circle cx="8" cy="8" r="8" fill="#7dc21e"/>
          <rect x="4" y="5" width="8" height="6" rx="1" fill="#1e1e1f"/>
          <path d="M4.3 5.4L8 8.3l3.7-2.9" stroke="#7dc21e" stroke-width="0.9" fill="none"/>
        </svg>
        halya.dorosh@quillmail.example
      </li>
      <li class="contact__item">
        <svg class="icon" viewBox="0 0 16 16" aria-hidden="true">
          <circle cx="8" cy="8" r="8" fill="#7dc21e"/>
          <circle cx="8" cy="8" r="4" fill="none" stroke="#1e1e1f" stroke-width="1.1"/>
          <path d="M4 8h8M8 4c-1.6 1.8-1.6 6.2 0 8M8 4c1.6 1.8 1.6 6.2 0 8" fill="none" stroke="#1e1e1f" stroke-width="0.9"/>
        </svg>
        www.brovix.example
      </li>
    </ul>
  </div>
</section>

</body>
</html>
```